Im open to ideas.. I was thinking on my business cards aswell as my logo. a place for my name. email. phone number and abn..

ive attched a file with my business logo. which i dont love the colours.. i was think a dark background with charcoal letters so something along those colour schumes but im open to ideas..

BRM Constructions

```html
<!DOCTYPE html>
<html lang="en">
<head>
<meta charset="UTF-8">
<title>BRM Constructions – Business Card</title>
<link href="https://fonts.googleapis.com/css2?family=Arimo:wght@400;700&display=swap" rel="stylesheet">
<style>
  :root {
    --backdrop: #3a3431;
    --card: #1c1c1d;
    --card-edge: #111112;
    --brand-grey: #c8c8c8;
    --brand-white: #f2f2f2;
    --accent-red: #d8201f;
    --text-light: #e6e6e6;
    --text-muted: #9a9a9a;
    --divider: #7a7a7a;
  }
  * { box-sizing: border-box; margin: 0; padding: 0; }
  html, body {
    width: 1200px;
    height: 787px;
    overflow: hidden;
  }
  body {
    background: var(--backdrop);
    font-family: "Arimo", Arial, sans-serif;
    display: flex;
    align-items: center;
    justify-content: center;
    gap: 40px;
  }
  .card {
    width: 540px;
    height: 309px;
    background: var(--card);
    border: 1px solid var(--card-edge);
    border-radius: 3px;
    box-shadow: 0 10px 28px rgba(0, 0, 0, 0.45);
    position: relative;
  }

  /* Front */
  .card-front {
    display: flex;
    flex-direction: column;
    align-items: center;
    justify-content: center;
    gap: 28px;
  }
  .brand {
    display: flex;
    align-items: center;
    gap: 12px;
  }
  .brand-mark {
    width: 16px;
    height: 16px;
    background: var(--accent-red);
  }
  .brand-name {
    font-weight: 700;
    letter-spacing: 1px;
    text-transform: uppercase;
    line-height: 1;
  }
  .card-front .brand-name {
    font-size: 36px;
    color: var(--brand-grey);
  }
  .website {
    font-size: 14px;
    letter-spacing: 5px;
    color: var(--text-light);
  }

  /* Back */
  .card-back {
    display: flex;
    align-items: center;
    padding: 0 34px 0 34px;
  }
  .card-back .brand {
    width: 268px;
    justify-content: center;
  }
  .card-back .brand-name {
    font-size: 27px;
    color: var(--brand-white);
  }
  .divider {
    width: 1px;
    height: 158px;
    background: var(--divider);
    margin: 0 24px 0 14px;
  }
  .contact {
    color: var(--text-light);
    font-size: 15px;
  }
  .contact-name {
    color: var(--accent-red);
    font-size: 19px;
    font-weight: 700;
    letter-spacing: 0.5px;
  }
  .contact-role {
    font-size: 16px;
    margin-top: 2px;
    margin-bottom: 14px;
  }
  .contact-abn {
    font-size: 14px;
    margin-bottom: 12px;
  }
  .contact-line {
    display: flex;
    align-items: center;
    gap: 10px;
    font-size: 14px;
    margin-top: 8px;
  }
  .contact-icon {
    width: 14px;
    height: 14px;
    flex: none;
    fill: var(--accent-red);
  }
</style>
</head>
<body>

  <section class="card card-front" aria-label="Business card front">
    <div class="brand">
      <span class="brand-mark"></span>
      <span class="brand-name">BRM Constructions</span>
    </div>
    <p class="website">www.brmbuild.example</p>
  </section>

  <section class="card card-back" aria-label="Business card back">
    <div class="brand">
      <span class="brand-mark"></span>
      <span class="brand-name">BRM Constructions</span>
    </div>
    <span class="divider"></span>
    <div class="contact">
      <p class="contact-name">Sam Porter</p>
      <p class="contact-role">President</p>
      <p class="contact-abn">ABN: 987654321</p>
      <p class="contact-line">
        <svg class="contact-icon" viewBox="0 0 24 24" aria-hidden="true">
          <path d="M6.6 10.8a15.1 15.1 0 0 0 6.6 6.6l2.2-2.2a1 1 0 0 1 1-.25 11.4 11.4 0 0 0 3.6.57 1 1 0 0 1 1 1V20a1 1 0 0 1-1 1A17 17 0 0 1 3 4a1 1 0 0 1 1-1h3.5a1 1 0 0 1 1 1c0 1.25.2 2.45.57 3.6a1 1 0 0 1-.25 1z"/>
        </svg>
        <span>555 0134 2268</span>
      </p>
      <p class="contact-line">
        <svg class="contact-icon" viewBox="0 0 24 24" aria-hidden="true">
          <path d="M2 5h20v14H2z M2 5l10 8 10-8" />
          <path d="M3 6.2l9 7.2 9-7.2V5H3z" fill="#1c1c1d"/>
        </svg>
        <span>sam@brmbuild.example</span>
      </p>
    </div>
  </section>

</body>
</html>
```